Bookmark Design

We would like to design a book mark with logos of our two business and a quote.

One side with the quote "The first wealth is health" - Tobias Kendrick Mallory and the two logos.

The back side has the two logos with its respective phone numbers and a common address (this is to be advised to the winner of the project).

```html
<!DOCTYPE html>
<html lang="en">
<head>
<meta charset="utf-8">
<title>Bookmark – The first wealth is health</title>
<link rel="stylesheet" href="https://fonts.googleapis.com/css2?family=Lora:ital,wght@1,500&family=Montserrat:wght@700&display=swap">
<style>
  :root {
    --page-bg: #e9ebee;
    --brand-blue: #0a4a9c;
    --brand-green: #62ad5b;
    --accent-green: #7cbf3a;
    --ring-grey: #5c5f62;
    --card-white: #f4f4f4;
    --ink-white: #ffffff;
    --shadow: rgba(20, 30, 50, 0.22);
  }
  * { margin: 0; padding: 0; box-sizing: border-box; }
  html, body { width: 1200px; height: 800px; overflow: hidden; }
  body {
    background: var(--page-bg);
    display: flex;
    align-items: center;
    justify-content: center;
  }
  .bookmark {
    position: relative;
    width: 290px;
    height: 740px;
    filter: drop-shadow(0 10px 18px var(--shadow));
  }
  .bookmark-shape { position: absolute; inset: 0; }
  .quote {
    position: absolute;
    top: 120px;
    left: 0;
    width: 100%;
    text-align: center;
    color: var(--ink-white);
    font-family: "Lora", Georgia, serif;
    font-style: italic;
    font-weight: 500;
  }
  .quote-mark {
    display: block;
    font-family: Georgia, "Times New Roman", serif;
    font-style: normal;
    font-weight: 700;
    line-height: 1;
  }
  .quote-mark--open { font-size: 48px; height: 30px; }
  .quote-mark--close { font-size: 80px; height: 50px; margin-top: 6px; }
  .quote-text { font-size: 27px; line-height: 1.2; letter-spacing: 0.5px; }
  .logo {
    position: absolute;
    left: 0;
    width: 100%;
    text-align: center;
    font-family: "Montserrat", Arial, sans-serif;
    font-weight: 700;
    text-transform: uppercase;
  }
  .logo--clinic { top: 380px; color: var(--brand-blue); }
  .logo--dental { top: 520px; color: var(--brand-green); }
  .logo-dot {
    display: block;
    width: 56px;
    height: 56px;
    margin: 0 auto 12px;
    border: 4px solid var(--brand-blue);
    border-radius: 50%;
  }
  .logo-name { font-size: 22px; line-height: 1.15; letter-spacing: 1px; }
  .logo-name small { display: block; font-size: 13px; letter-spacing: 5px; }
</style>
</head>
<body>
  <main class="bookmark">
    <svg class="bookmark-shape" viewBox="0 0 290 740" width="290" height="740" aria-hidden="true">
      <defs>
        <clipPath id="tag-outline">
          <path d="M0 80 L60 0 H230 L290 80 V740 H0 Z"/>
        </clipPath>
      </defs>
      <g clip-path="url(#tag-outline)">
        <rect class="band-blue" x="0" y="0" width="290" height="740" fill="var(--brand-blue)"/>
        <rect class="band-green" x="0" y="560" width="290" height="180" fill="var(--brand-green)"/>
        <circle class="centre-disc" cx="145" cy="500" r="210" fill="var(--card-white)" stroke="var(--accent-green)" stroke-width="6"/>
        <path class="centre-disc-rim" d="M-65 500 A210 210 0 0 0 355 500" fill="none" stroke="var(--ring-grey)" stroke-width="6"/>
      </g>
      <circle class="eyelet" cx="145" cy="40" r="10" fill="none" stroke="#b9903a" stroke-width="4"/>
      <circle class="eyelet-hole" cx="145" cy="40" r="7" fill="var(--page-bg)"/>
    </svg>

    <blockquote class="quote">
      <span class="quote-mark quote-mark--open">&ldquo;</span>
      <p class="quote-text">The first<br>wealth is health</p>
      <span class="quote-mark quote-mark--close">&rdquo;</span>
    </blockquote>

    <div class="logo logo--clinic">
      <span class="logo-dot"></span>
      <p class="logo-name">Harrowfield<small>Clinic</small></p>
    </div>

    <div class="logo logo--dental">
      <p class="logo-name">Midtown<br>Dental<small>Harrowfield</small></p>
    </div>
  </main>
</body>
</html>
```